Accountancy firm needs clean and simple website and optional logo

We need a logo and basic wordpress website design for a Sydney based accountancy firm.
We need a clean and simple logo and website, based on the accounting/finance/tax industry. Simple, credible and official colors.
The logo is expected to be so simple that we have combined into the one job.
If you submit a logo design and we choose it along with someone else's website design you will be paid a bonus of $60. The website design will still win the competition as per normal.
Current website is old and terrible but gives you an idea of the sitemap (super simple) and what they do: www.brookfiscal.com.au
We want original different to normal template looking designs.
We like videos, and like http://www.merivane.com.au/
Feel free to go to clipvault9 and use some videos from there.
We are based in Sydney Australia and in the field of taxation and accounting
We want a clean, formal, credible site, limited pages.
The project is guaranteed, so go for it.
Logo Text
Brook & Associates

```html
<!DOCTYPE html>
<html lang="en">
<head>
<meta charset="utf-8">
<title>Brook &amp; Associates – Tax Accountants</title>
<link rel="stylesheet" href="https://fonts.googleapis.com/css2?family=Raleway:wght@400;500;600;700&family=Open+Sans:wght@400;600&display=swap">
<style>
:root{
  --blue:#0a86d8;
  --blue-deep:#0a6fc2;
  --blue-light:#2aa3ea;
  --ink:#1c1c1c;
  --muted:#7a7a7a;
  --line:#d9d9d9;
  --steel:#a5afb9;
  --footer:#222222;
  --white:#ffffff;
}
*{margin:0;padding:0;box-sizing:border-box}
html,body{width:898px;height:1200px;overflow:hidden;background:var(--white)}
body{position:relative;font-family:"Open Sans",Arial,sans-serif;color:var(--ink)}
.abs{position:absolute}

/* header */
.brand-mark{left:144px;top:14px;width:64px;height:64px;background:var(--blue)}
.brand-name{left:218px;top:53px;font-family:"Raleway",Arial,sans-serif;font-weight:700;font-size:11px;letter-spacing:.3px;color:var(--ink)}
.brand-tag{left:218px;top:67px;font-size:10px;color:var(--ink)}
.call-label{right:145px;top:45px;font-family:"Raleway",Arial,sans-serif;font-size:9px;font-weight:500;color:var(--blue)}
.call-number{right:145px;top:57px;font-family:"Raleway",Arial,sans-serif;font-size:16.5px;font-weight:500;color:var(--ink);display:flex;align-items:center;gap:3px}

/* navigation */
.main-nav{left:0;top:90px;width:898px;height:34px;background:linear-gradient(#2ea6ec,#0a7fd2)}
.nav-item{position:absolute;top:0;height:34px;line-height:34px;transform:translateX(-50%);font-family:"Raleway",Arial,sans-serif;font-weight:600;font-size:12px;color:var(--white)}
.nav-sep{position:absolute;top:0;width:1px;height:34px;background:rgba(0,0,0,.15);box-shadow:1px 0 0 rgba(255,255,255,.2)}

/* hero */
.hero{left:0;top:124px;width:898px;height:386px;background:linear-gradient(100deg,#dfe7ef 0%,#c9d6e2 40%,#a9907e 62%,#6c7c86 80%,#c98a4f 100%)}
.hero-title{left:143px;top:255px;font-family:"Raleway",Arial,sans-serif;font-size:33px;font-weight:400;color:#111}
.hero-sub{left:143px;top:302px;font-family:"Raleway",Arial,sans-serif;font-size:17.5px;font-weight:600;color:var(--blue-light)}
.hero-arrow{top:268px}

/* welcome */
.welcome-title{left:0;width:898px;text-align:center;font-family:"Raleway",Arial,sans-serif;font-weight:500;color:var(--ink)}
.welcome-copy{left:160px;top:602px;width:578px;text-align:center;font-size:7.3px;line-height:13px;color:var(--muted)}

/* service cards */
.card{top:676px;width:192px;height:220px;border:1px solid var(--line);background:var(--white)}
.card-photo{position:absolute;left:-1px;top:-1px;width:192px;height:106px;display:flex;align-items:center;justify-content:center}
.card-title{position:absolute;left:0;top:118px;width:190px;text-align:center;font-family:"Raleway",Arial,sans-serif;font-size:14px;font-weight:500;color:var(--blue)}
.card-copy{position:absolute;left:14px;top:140px;width:162px;text-align:center;font-size:7.4px;line-height:13px;color:var(--muted)}
.card-btn{position:absolute;left:62px;top:186px;width:66px;height:19px;line-height:19px;text-align:center;background:linear-gradient(#1f94e2,#0a6fc2);border-radius:2px;font-size:7.5px;color:var(--white)}

/* feature panels */
.feature-photo{top:928px;width:142px;height:138px}
.feature-panel{top:928px;width:156px;height:138px;padding:23px 16px 0 16px;color:var(--white)}
.feature-panel.steel{background:var(--steel)}
.feature-panel.accent{background:var(--blue)}
.feature-title{font-family:"Raleway",Arial,sans-serif;font-size:15px;font-weight:500;letter-spacing:.3px}
.feature-sub{margin-top:3px;font-family:"Raleway",Arial,sans-serif;font-size:8.5px;font-weight:600}
.feature-copy{margin-top:8px;font-size:7.3px;line-height:13px;opacity:.9}

/* footer */
.site-footer{left:0;top:1114px;width:898px;height:86px;background:var(--footer)}
.footer-links{left:141px;top:1137px;font-family:"Raleway",Arial,sans-serif;font-size:9px;font-weight:500;color:var(--white);letter-spacing:.2px}
.footer-copy{left:141px;top:1157px;font-size:7.8px;color:#9a9a9a}
.social{top:1136px;width:22px;height:22px;border-radius:50%;border:2px solid #eaeaea}
</style>
</head>
<body>

<header>
  <div class="abs brand-mark"></div>
  <div class="abs brand-name">BROOK &amp; ASSOCIATES</div>
  <div class="abs brand-tag">tax accountants</div>
  <div class="abs call-label">CALL US TODAY</div>
  <div class="abs call-number">
    <svg width="13" height="14" viewBox="0 0 24 24"><path fill="#0a86d8" d="M6.6 10.8c1.4 2.8 3.8 5.1 6.6 6.6l2.2-2.2c.3-.3.7-.4 1-.2 1.1.4 2.3.6 3.6.6.6 0 1 .4 1 1V20c0 .6-.4 1-1 1C10.6 21 3 13.4 3 4c0-.6.4-1 1-1h3.5c.6 0 1 .4 1 1 0 1.2.2 2.4.6 3.6.1.3 0 .7-.2 1L6.6 10.8z"/></svg>
    02 9471 2250
  </div>
</header>

<nav class="abs main-nav">
  <span class="nav-item" style="left:200px">HOME</span>
  <span class="nav-sep" style="left:241px"></span>
  <span class="nav-item" style="left:296px">ABOUT US</span>
  <span class="nav-sep" style="left:350px"></span>
  <span class="nav-item" style="left:405px">PROJECTS</span>
  <span class="nav-sep" style="left:458px"></span>
  <span class="nav-item" style="left:512px">SERVICES</span>
  <span class="nav-sep" style="left:572px"></span>
  <span class="nav-item" style="left:607px">NEWS</span>
  <span class="nav-item" style="left:702px">CONTACT</span>
</nav>

<section>
  <div class="abs hero" role="img" aria-label="Photo of a smiling senior couple seated on wooden deck chairs by the water"></div>
  <svg class="abs hero-arrow" style="left:98px" width="20" height="46" viewBox="0 0 20 46"><path d="M18 2 L2 23 L18 44" fill="none" stroke="#111" stroke-width="1.5"/></svg>
  <svg class="abs hero-arrow" style="left:768px" width="20" height="46" viewBox="0 0 20 46"><path d="M2 2 L18 23 L2 44" fill="none" stroke="#111" stroke-width="1.5"/></svg>
  <div class="abs hero-title">TAX &amp; ACCOUNTING</div>
  <div class="abs hero-sub">PRAESENT AMET EST DICTUM</div>
</section>

<section>
  <div class="abs welcome-title" style="top:544px;font-size:21px">WELCOME TO BROOK &amp; ASSOCIATES</div>
  <div class="abs welcome-title" style="top:568px;font-size:19px">TAX ACCOUNTANTS</div>
  <p class="abs welcome-copy">Mauris vel lacus vitae felis vestibulum volutpat E eu imperdiet ac nisl Cum sociis natoque penatibus et magnis dis parturient montes nascetur ridiculus mus In iaculis facilisis massa Etiam eu urna Sed porta Suspendisse quam leo molestie sed luctus quis feugiat in pede Fusce tellus Sed metus augue convallis et vehicula ut pulvinar eu ante Integer orci tellus tristique vitae consequat nec Vivamus porttitor purus nisi eleifend libero a tempus libero lectus feugiat</p>
</section>

<section>
  <div class="abs card" style="left:149px">
    <div class="card-photo" role="img" aria-label="Photo of a tax form with glasses and a pen" style="background:linear-gradient(120deg,#6b6f74,#4b4e53 60%,#5d5452)">
      <svg width="60" height="60" viewBox="0 0 60 60"><circle cx="30" cy="30" r="28" fill="none" stroke="#fff" stroke-width="1.6"/><path d="M22 18h12l6 6v18H22z" fill="none" stroke="#fff" stroke-width="1.5"/><circle cx="27" cy="26" r="1.8" fill="none" stroke="#fff"/><circle cx="34" cy="33" r="1.8" fill="none" stroke="#fff"/><path d="M35 24 26 35" stroke="#fff" stroke-width="1.3"/><path d="M25 39l3 3 6-6" fill="none" stroke="#fff" stroke-width="1.3"/></svg>
    </div>
    <div class="card-title">TAX SERVICES</div>
    <p class="card-copy">rdum nec interdum vel blandit sed nulla In ullamcorper est eget tempor cursus neque mi facilisis volutpat in imperdiet sit</p>
    <div class="card-btn">READ MORE</div>
  </div>

  <div class="abs card" style="left:355px">
    <div class="card-photo" role="img" aria-label="Photo of an adviser meeting with a couple" style="background:linear-gradient(120deg,#7d7a76,#5a5c62 55%,#3d4150)">
      <svg width="60" height="60" viewBox="0 0 60 60"><circle cx="30" cy="30" r="28" fill="none" stroke="#fff" stroke-width="1.6"/><rect x="21" y="17" width="18" height="26" rx="2" fill="none" stroke="#fff" stroke-width="1.5"/><rect x="24" y="20" width="12" height="5" fill="#fff"/><g fill="#fff"><rect x="24" y="28" width="3" height="3"/><rect x="28.5" y="28" width="3" height="3"/><rect x="33" y="28" width="3" height="3"/><rect x="24" y="33" width="3" height="3"/><rect x="28.5" y="33" width="3" height="3"/><rect x="33" y="33" width="3" height="3"/><rect x="24" y="38" width="3" height="3"/><rect x="28.5" y="38" width="3" height="3"/><rect x="33" y="38" width="3" height="3"/></g></svg>
    </div>
    <div class="card-title">ACCOUNTING</div>
    <p class="card-copy">rdum nec interdum vel blandit sed nulla In ullamcorper est eget tempor cursus neque mi facilisis volutpat in imperdie</p>
    <div class="card-btn">READ MORE</div>
  </div>

  <div class="abs card" style="left:560px">
    <div class="card-photo" role="img" aria-label="Photo of hands reviewing financial reports at a desk" style="background:linear-gradient(120deg,#4c5057,#6e7278 55%,#585c63)">
      <svg width="60" height="60" viewBox="0 0 60 60"><circle cx="30" cy="30" r="28" fill="none" stroke="#fff" stroke-width="1.6"/><rect x="17" y="20" width="26" height="17" fill="none" stroke="#fff" stroke-width="1.5"/><path d="M30 37v4M24 42h12" stroke="#fff" stroke-width="1.5"/><g fill="#fff"><rect x="20" y="30" width="2" height="4"/><rect x="23" y="27" width="2" height="7"/><rect x="26" y="29" width="2" height="5"/></g><path d="M35 24a4.5 4.5 0 1 0 4.5 4.5H35z" fill="#fff"/></svg>
    </div>
    <div class="card-title">FINANCE SERVICE</div>
    <p class="card-copy">rdum nec interdum vel blandit sed nulla In ullamcorper est eget tempor cursus neque mi facilisis volutpat in imperdiet sit</p>
    <div class="card-btn">READ MORE</div>
  </div>
</section>

<section>
  <div class="abs feature-photo" style="left:149px;background:linear-gradient(135deg,#d7dde3,#8e96a0 50%,#c9d4dc)" role="img" aria-label="Photo of a business team around a meeting table"></div>
  <div class="abs feature-panel steel" style="left:291px">
    <div class="feature-title">HOW WE WORK</div>
    <div class="feature-sub">VIEW OUR PROJECTS</div>
    <p class="feature-copy">Rdum nec interdum vel blandit sed nulla In ullamcorper est eget tempor cursus neque mi facilisis volutpat in imperdiet sit</p>
  </div>
  <div class="abs feature-photo" style="left:458px;background:linear-gradient(135deg,#c5d3dd,#8fa4b4 50%,#dfe6ec)" role="img" aria-label="Photo of a smiling young team member in an office"></div>
  <div class="abs feature-panel accent" style="left:600px">
    <div class="feature-title">OUR TEAM</div>
    <div class="feature-sub">MEET OUR TEAM MEMBER</div>
    <p class="feature-copy">Rdum nec interdum vel blandit sed nulla In ullamcorper est eget tempor cursus neque mi facilisis volutpat in imperdiet sit</p>
  </div>
</section>

<footer>
  <div class="abs site-footer"></div>
  <div class="abs footer-links">HOME &nbsp;|&nbsp; ABOUT &nbsp;US &nbsp;|&nbsp; SERVICES &nbsp;|&nbsp; OUR PROJECTS &nbsp;|&nbsp; CONTACT US</div>
  <div class="abs footer-copy">© 2015 Company Name &nbsp;All right reserved &nbsp;Term of Use</div>
  <span class="abs social" style="left:653px;background:#3fa9e0"></span>
  <span class="abs social" style="left:678px;background:#2d5aa6"></span>
  <span class="abs social" style="left:703px;background:#1b7fb8"></span>
  <span class="abs social" style="left:728px;background:#d9483a"></span>
</footer>

</body>
</html>
```